Tall Fern Roofing Business Card

Need a business card with the logo that was designed here

Contact Information for Business Card

Name, Title, Phone, Email, Website, Company name

```html
<!DOCTYPE html>
<html lang="en">
<head>
<meta charset="utf-8">
<title>Tall Fern Roofing Business Card</title>
<link href="https://fonts.googleapis.com/css2?family=Montserrat:wght@400;500;700&display=swap" rel="stylesheet">
<style>
  :root {
    --page-bg: #1d1d1d;
    --card-bg: #0c0c0c;
    --brand-blue: #1f7fd0;
    --silver: #c9c9c9;
    --text-grey: #bdbdbd;
    --divider: #1f7fd0;
  }
  * { margin: 0; padding: 0; box-sizing: border-box; }
  html, body { width: 1200px; height: 900px; overflow: hidden; }
  body {
    background: var(--page-bg);
    font-family: "Montserrat", sans-serif;
    display: flex;
    flex-direction: column;
    align-items: center;
    justify-content: center;
    gap: 40px;
  }
  .card {
    width: 700px;
    height: 400px;
    background: var(--card-bg);
    border-radius: 26px;
    position: relative;
    display: flex;
    align-items: center;
  }
  .card--front { padding: 0 56px; }
  .brand-block {
    width: 300px;
    display: flex;
    align-items: center;
    gap: 12px;
  }
  .brand-mark {
    width: 16px; height: 16px;
    background: var(--brand-blue);
    flex-shrink: 0;
  }
  .brand-name {
    font-weight: 700;
    font-size: 28px;
    line-height: 1.15;
    color: var(--brand-blue);
  }
  .divider {
    width: 2px;
    height: 200px;
    margin: 0 36px 0 8px;
    background: linear-gradient(to bottom, transparent, var(--divider) 30%, var(--divider) 70%, transparent);
  }
  .contact-block { display: flex; flex-direction: column; }
  .person-name {
    font-weight: 700;
    font-size: 22px;
    color: var(--brand-blue);
    text-transform: uppercase;
    letter-spacing: 0.5px;
  }
  .person-title {
    font-weight: 400;
    font-size: 16px;
    color: var(--text-grey);
    margin-top: 2px;
    margin-bottom: 30px;
  }
  .contact-list { list-style: none; display: flex; flex-direction: column; gap: 8px; }
  .contact-item {
    display: flex; align-items: center; gap: 10px;
    font-size: 16px; color: var(--text-grey);
  }
  .contact-item svg { width: 16px; height: 16px; fill: var(--brand-blue); flex-shrink: 0; }
  .contact-item .accent { color: var(--brand-blue); }
  .card--back { justify-content: center; }
  .card--back .brand-block { width: auto; }
  .card--back .brand-name { color: var(--silver); font-size: 36px; }
  .card--back .brand-mark { background: var(--silver); width: 20px; height: 20px; }
</style>
</head>
<body>
  <section class="card card--front">
    <div class="brand-block">
      <span class="brand-mark"></span>
      <span class="brand-name">Tall Fern Roofing</span>
    </div>
    <div class="divider"></div>
    <div class="contact-block">
      <p class="person-name">Marcus Reed</p>
      <p class="person-title">Managing Director</p>
      <ul class="contact-list">
        <li class="contact-item">
          <svg viewBox="0 0 24 24"><path d="M6.6 10.8a15.1 15.1 0 0 0 6.6 6.6l2.2-2.2c.3-.3.7-.4 1-.2 1.1.4 2.3.6 3.6.6.6 0 1 .4 1 1V20c0 .6-.4 1-1 1C10.6 21 3 13.4 3 4c0-.6.4-1 1-1h3.5c.6 0 1 .4 1 1 0 1.3.2 2.5.6 3.6.1.3 0 .7-.2 1z"/></svg>
          <span>044-987 654 321</span>
        </li>
        <li class="contact-item">
          <svg viewBox="0 0 24 24"><path d="M2 5h20v14H2z M2 5l10 8 10-8" fill="none" stroke="#1f7fd0" stroke-width="2"/></svg>
          <span>info@tallfernroof.com</span>
        </li>
        <li class="contact-item">
          <svg viewBox="0 0 24 24"><circle cx="12" cy="12" r="9" fill="none" stroke="#1f7fd0" stroke-width="2"/><path d="M3 12h18M12 3c3 3 3 15 0 18M12 3c-3 3-3 15 0 18" fill="none" stroke="#1f7fd0" stroke-width="1.6"/></svg>
          <span>www.<span class="accent">tallfernroof</span>.com</span>
        </li>
      </ul>
    </div>
  </section>

  <section class="card card--back">
    <div class="brand-block">
      <span class="brand-mark"></span>
      <span class="brand-name">Tall Fern Roofing</span>
    </div>
  </section>
</body>
</html>
```